Business cards to launch an education platform

Hi,
I am looking at having new business cards designed.
I am a startup, developing a web platform for schools and university, the education world. It's an online assessment system.
I would like a card that looks classy, and that is using the colors and the font of my logo.

I have attached:
1) my logo
2) A business card that I have designed quickly so you can have all the information required in the card, but I really don't like it.
3) The font that I am using (Lato Regular) to design my web platform
4) Some screenshots of my web platform so you can have a look at the style that I have.

Target Market(s)

Major market: Education system: Schools and university
Minor markets: Business in general

Industry/Entity Type

Business

Contact Information for Business Card

Clara Fenwick
Director

M: 0437 518 902
E: clara.fenwick@amberLoomSystems.com.au

Requirements
Must have
• The colors of my logo

```html
<!DOCTYPE html>
<html lang="en">
<head>
<meta charset="utf-8">
<title>Amber Loom Systems — Business Cards</title>
<link rel="stylesheet" href="https://fonts.googleapis.com/css2?family=Lato:wght@400;700&display=swap">
<style>
  :root {
    --page-bg: #eceef1;
    --navy: #0f4a7c;
    --navy-deep: #0b3a63;
    --brand-blue: #1f5f99;
    --sky: #29c4ea;
    --sky-light: #5ad6f2;
    --mid-blue: #1a86c8;
    --ink: #1b4f86;
    --white: #ffffff;
    --card-shadow: 0 14px 30px rgba(20, 40, 70, 0.22);
  }
  * { box-sizing: border-box; margin: 0; padding: 0; }
  html, body {
    width: 1200px;
    height: 950px;
    overflow: hidden;
    background: var(--page-bg);
    font-family: "Lato", Arial, sans-serif;
  }
  .sheet {
    position: relative;
    width: 1200px;
    height: 950px;
  }
  .card {
    position: absolute;
    left: 250px;
    width: 700px;
    height: 400px;
    border-radius: 4px;
    overflow: hidden;
    box-shadow: var(--card-shadow);
  }

  /* Back of card */
  .card-back {
    top: 60px;
    background: linear-gradient(135deg, var(--navy) 0%, var(--navy-deep) 100%);
    color: var(--white);
  }
  .card-back .brand {
    position: absolute;
    top: 150px;
    left: 0;
    width: 100%;
    display: flex;
    justify-content: center;
    align-items: center;
    gap: 14px;
  }
  .card-back .brand-square {
    width: 34px;
    height: 34px;
    background: var(--white);
  }
  .card-back .brand-name {
    font-size: 34px;
    font-weight: 400;
    letter-spacing: 1px;
    color: var(--white);
  }
  .card-back .website {
    position: absolute;
    bottom: 48px;
    width: 100%;
    text-align: center;
    font-size: 17px;
    letter-spacing: 0.5px;
    color: var(--white);
  }

  /* Front of card */
  .card-front {
    top: 490px;
    background: var(--white);
  }
  .card-front .brand {
    position: absolute;
    top: 72px;
    left: 120px;
    display: flex;
    align-items: center;
    gap: 16px;
  }
  .card-front .brand-square {
    width: 58px;
    height: 58px;
    background: var(--brand-blue);
  }
  .card-front .brand-name {
    font-size: 38px;
    font-weight: 400;
    letter-spacing: 1.5px;
    color: var(--ink);
  }
  .contact-band {
    position: absolute;
    left: 275px;
    right: 0;
    top: 200px;
    bottom: 0;
    background: linear-gradient(90deg, var(--sky) 0%, var(--sky-light) 100%);
    color: var(--white);
    padding: 22px 26px 0 0;
    text-align: right;
    font-size: 17px;
    line-height: 1.9;
  }
  .contact-line {
    display: flex;
    justify-content: flex-end;
    align-items: center;
    gap: 10px;
  }
  .contact-line svg { flex: none; }
  .name-block {
    position: absolute;
    left: 0;
    width: 275px;
    top: 285px;
    bottom: 0;
    background: linear-gradient(135deg, var(--mid-blue) 0%, var(--brand-blue) 100%);
    color: var(--white);
    padding: 30px 0 0 28px;
    border-right: 3px solid var(--white);
  }
  .person-name {
    font-size: 22px;
    font-weight: 700;
    letter-spacing: 0.5px;
    text-transform: uppercase;
  }
  .person-role {
    font-size: 15px;
    letter-spacing: 0.5px;
    text-transform: uppercase;
    margin-top: 4px;
  }
</style>
</head>
<body>
<main class="sheet">
  <section class="card card-back" aria-label="Card back">
    <div class="brand">
      <span class="brand-square"></span>
      <span class="brand-name">Amber Loom Systems</span>
    </div>
    <p class="website">www.amberLoomSystems.com.au</p>
  </section>

  <section class="card card-front" aria-label="Card front">
    <div class="brand">
      <span class="brand-square"></span>
      <span class="brand-name">Amber Loom Systems</span>
    </div>

    <div class="contact-band">
      <p class="contact-line">
        <span>0437 518 902</span>
        <svg width="12" height="18" viewBox="0 0 12 18" aria-hidden="true">
          <rect x="1" y="1" width="10" height="16" rx="2" fill="none" stroke="#ffffff" stroke-width="1.6"/>
          <circle cx="6" cy="14" r="1" fill="#ffffff"/>
        </svg>
      </p>
      <p class="contact-line">
        <span>clara.fenwick@amberLoomSystems.com.au</span>
        <svg width="16" height="12" viewBox="0 0 16 12" aria-hidden="true">
          <rect x="0.8" y="0.8" width="14.4" height="10.4" fill="#ffffff"/>
          <path d="M1 1 L8 7 L15 1" fill="none" stroke="#29c4ea" stroke-width="1.4"/>
        </svg>
      </p>
    </div>

    <div class="name-block">
      <p class="person-name">Clara Fenwick</p>
      <p class="person-role">Director</p>
    </div>
  </section>
</main>
</body>
</html>
```